COMPANY NAME: Bright Harbor Ventures: Task Description: We are a new UK based business with global rea

Target Market

- Personal and professional development – 30-55 age group, corporate leaders, Eastern European and Asian markets
- On-assignment projects – Corporate market – Eastern European and Asian Markets
- Property investment - 35-65 age group, Europe, USA, Australia

What we need

We need logos and brand design for a suite of web platforms (website, twitter and Facebook profile). We would like to have a cohesive and consistent look across all of our online platforms. The design suite must therefore include social media logos, backgrounds and headers. Specifically we are looking for:

a. Facebook header/page design: likely to have a more youthful look

b. Website: Header, background and layout that is responsive to devices, iPhone primarily, then tablet, then PC (we have purchased a website building package from SiteKettle so if you are familiar with one of their themes, it would be great to have a design that fits with a theme you would recommend); Design should be able to accommodate a place to position video in the medium term but an image in the short term.

c. LinkedIn: header/logo; more corporate look

d. Twitter: background/logo

e. Powerpoint template: background and logo - simple and soft background not busy

f. Electronic Newsletter: logo, header and sidebar; simple and soft background not busy

h. Business card: sophisticated and simple

Colors

We have in mind a preference for colors from the purple family, maybe lavender, so as to appeal to all genders and age groups. Though we are happy to go with a recommendation if you think otherwise.

We would like a look that is professional, airy, bright, fresh, futuristic, insightful, friendly.

Ethos of the brand

- experiencing opportunity and being fulfilled in a changing world
- services are facilitated through insights
- support provided through our product, services and tailored approach to coaching/partnerships (which includes private client match-making)
- we are service providers and passionate about quality and modern leadership skills at all stages in life.

The company name is "Bright Harbor Ventures” - our main message is helping people move to the next level - through investments, personal and professional growth.

Some of our messaging

1. International Leadership in a new world.

2. New technology;

3. Informed;

4. Positively Influential

5. Making a difference;

6. Empowered;

7. Risk free investments;

8. Commercial opportunity;

9. Fulfilled living;

10. Carefree and Fun Living;

11. Progression;

12. Open-minded

13. Energy/dynamic

The Business:
The business is to move people very quickly out of situations that hold them back. the situations could be their own personal situations; their career; their jobs; their teams; their ideas; their finances; their financial opportunities. Remove their fears and give them the strategies to take action. The team are international and have 40 years experience between them in this area.

We do want to come across modern and dynamic, customer outcome focussed, building long-term relationships; international.
Updates

Project Deadline Extended
Reason: We have not found the right designs - we are not just looking for a website design but also images and logos. Most images we can see in the designs are stock images - very standard. We need an image which will be the face of the company, like the shop front window. This main image will be used on social media (top image) and also the home page of the website.

Target Market(s)

30-55 years
Eastern Europe; UK; Asia; Africa; Middle East
Personal, Professional, Corporate, and Financial Growth

Industry/Entity Type

Business Service

Contact Information for Business Card

Simple and stylish
the 3 areas of the business on the reverse -

International look - Offices in UK and San Francisco

Company name
web address www.brightharborventure.com
email director@brightharborventure.com
Facebook bright harbor venture
LinkedIn Bright Harbor Venture
Twitter Bright Harbor Venture
Telephone: +44 (0) 768 213 5597

Logo Text

Something that symbolises unlimited growth - probably not text - could use the word INSIGHT in some way

Number of Pages Required

1 page

Colors
e4daeb
f3f1f8
ffffff

Requirements
Must have
• social media symbols and address
• company name
• Melanie Thorpe
• Director
• Telephone +44 (0) 768 213 5597
• Website name www.brightharborventure.co.uk
• Reverse of Card:
• Discreet, Fast, Bright Harbor Consultancy
• Corporate, Professional, Personal & Property Investment
Nice to have
• not too angular; soft lines; not too cluttered (possibly social media on the reverse and just logo, name, number on the front?
Should not have
• too busy

```html
<!DOCTYPE html>
<html lang="en">
<head>
<meta charset="utf-8">
<title>Bright Harbor Venture</title>
<link rel="stylesheet" href="https://fonts.googleapis.com/css2?family=Montserrat:wght@300;400;500;600;700&family=Open+Sans:wght@400;600&display=swap">
<style>
  :root {
    --lavender: #e4daeb;
    --mist: #f3f1f8;
    --white: #ffffff;
    --ink: #2b2630;
    --text: #222222;
    --accent: #8a3fb0;
    --accent-bright: #b27ee6;
    --night: #1f1a20;
    --night-bar: #302a31;
    --muted-icon: #9d97a3;
  }
  * { box-sizing: border-box; margin: 0; padding: 0; }
  html, body { width: 842px; height: 1200px; overflow: hidden; background: var(--white); }
  body { position: relative; font-family: "Open Sans", Arial, sans-serif; color: var(--text); }
  .abs { position: absolute; }

  /* Header */
  .site-header { position: absolute; left: 0; top: 0; width: 842px; height: 57px; background: var(--lavender); }
  .brand { position: absolute; left: 114px; top: 17px; font-family: "Montserrat", Arial, sans-serif; font-size: 20px; font-weight: 400; color: var(--ink); letter-spacing: 0.1px; }
  .menu-toggle { position: absolute; left: 683px; top: 21px; display: flex; align-items: center; gap: 6px; font-family: "Montserrat", Arial, sans-serif; font-size: 10px; font-weight: 500; color: var(--ink); }
  .menu-dropdown { position: absolute; left: 653px; top: 45px; width: 76px; height: 121px; background: var(--lavender); list-style: none; padding-top: 3px; z-index: 2; }
  .menu-dropdown li { font-family: "Montserrat", Arial, sans-serif; font-size: 7px; color: var(--ink); height: 15.8px; line-height: 15.8px; padding-left: 20px; position: relative; }
  .menu-dropdown li::before { content: "›"; position: absolute; left: 8px; font-size: 8px; }

  /* Hero */
  .hero { position: absolute; left: 0; top: 57px; width: 842px; height: 342px;
    background: radial-gradient(ellipse at 72% 70%, #c99a82 0%, #7d6a6e 18%, rgba(40,52,80,0) 38%),
                linear-gradient(100deg, #0f1a2e 0%, #1c2a45 45%, #243352 70%, #131d33 100%); }
  .hero-title { position: absolute; left: 114px; top: 163px; width: 300px; font-family: "Montserrat", Arial, sans-serif; font-weight: 600; font-size: 21px; line-height: 25.5px; color: var(--white); }
  .hero-video-link { position: absolute; left: 114px; top: 315px; display: flex; align-items: center; gap: 7px; font-family: "Montserrat", Arial, sans-serif; font-size: 11px; color: var(--accent-bright); text-decoration: underline; }

  /* About */
  .about-title { position: absolute; left: 120px; top: 428px; font-family: "Montserrat", Arial, sans-serif; font-size: 26px; font-weight: 500; color: #111; letter-spacing: 0.3px; }
  .about-copy { position: absolute; left: 118px; top: 469px; width: 365px; font-size: 7.2px; line-height: 12.8px; color: #111; }
  .about-copy p { margin-bottom: 12.6px; }
  .btn { position: absolute; display: block; background: var(--lavender); font-family: "Montserrat", Arial, sans-serif; font-size: 8.5px; font-weight: 600; color: var(--ink); text-align: center; line-height: 24px; height: 24px; }
  .about-photo { position: absolute; left: 487px; top: 426px; width: 242px; height: 187px; background: linear-gradient(120deg, #e9edf3 0%, #b9c4d3 35%, #5f6f8a 65%, #2e3b55 100%); }

  /* Services */
  .services { position: absolute; left: 0; top: 668px; width: 842px; height: 337px; background: var(--lavender); }
  .service-card { position: absolute; top: 32px; width: 198px; height: 254px; background: var(--mist); }
  .service-title { position: absolute; left: 0; top: 13px; width: 100%; text-align: center; font-family: "Montserrat", Arial, sans-serif; font-size: 15px; font-weight: 500; line-height: 19px; color: #111; letter-spacing: 0.2px; }
  .service-icon { position: absolute; left: 50%; top: 73px; transform: translateX(-50%); }
  .service-list { position: absolute; left: 24px; top: 131px; list-style: none; }
  .service-list li { font-size: 8.4px; height: 20.4px; line-height: 12px; color: #222; padding-left: 14px; position: relative; white-space: nowrap; }
  .service-list li::before { content: ""; position: absolute; left: 0; top: 3.5px; width: 4px; height: 4px; border: 1px solid #333; border-radius: 50%; }
  .service-list li.highlight { color: var(--accent); }
  .service-card .btn { left: 24px; top: 216px; width: 68px; }

  /* Contact band */
  .contact-band { position: absolute; left: 0; top: 1005px; width: 842px; height: 143px; background: var(--night); }
  .contact-heading { position: absolute; left: 0; top: 26px; width: 842px; text-align: center; font-family: "Montserrat", Arial, sans-serif; font-weight: 400; font-size: 17px; line-height: 21px; color: #eeeaf0; }
  .contact-bar { position: absolute; left: 209px; top: 92px; width: 426px; height: 26px; background: var(--night-bar); display: flex; align-items: center; padding-left: 19px; gap: 8px; font-family: "Montserrat", Arial, sans-serif; font-size: 10.5px; color: #e6e2e8; }
  .contact-bar .gap { width: 14px; }

  /* Legal footer */
  .legal { position: absolute; left: 0; top: 1148px; width: 842px; height: 52px; background: var(--mist); }
  .legal-company { position: absolute; left: 0; top: 15px; width: 842px; text-align: center; font-family: "Montserrat", Arial, sans-serif; font-size: 9.3px; color: #111; display: flex; justify-content: center; align-items: center; gap: 7px; }
  .legal-copy { position: absolute; left: 0; top: 35px; width: 842px; text-align: center; font-size: 6px; color: #222; }
</style>
</head>
<body>

<header class="site-header">
  <div class="brand">Bright Harbor Venture</div>
  <div class="menu-toggle">Menu
    <svg width="15" height="12" viewBox="0 0 15 12"><rect y="0" width="15" height="2" fill="#8f8a95"/><rect y="5" width="15" height="2" fill="#8f8a95"/><rect y="10" width="15" height="2" fill="#8f8a95"/></svg>
  </div>
</header>

<ul class="menu-dropdown">
  <li>About You</li><li>About Us</li><li>Our Values</li><li>Testimonials</li><li>Social Media</li><li>News Alert</li><li>Contact Us</li>
</ul>

<section class="hero" role="img" aria-label="Businessman in a dark suit holding open hands with white people icons floating above them">
</section>
<h1 class="hero-title abs">Hello and welcome to the company that works with you on your terms</h1>
<div class="hero-video-link">
  <svg width="12" height="12" viewBox="0 0 12 12"><circle cx="6" cy="6" r="6" fill="#a25bd8"/><path d="M4.6 3.4 L8.6 6 L4.6 8.6 Z" fill="#1c2a45"/></svg>
  Watch our Video to play now
</div>

<h2 class="about-title">ABOUT US</h2>
<div class="about-copy">
  <p>If you seek an experienced and trusted partner to work with you on an assignment or simply want some strategies to move your personal or professional talents to the next level then you are in the right place.</p>
  <p>If you feel that the pace of change in business is so fast that to be an outstanding leader you should ensure you are brought up to speed regularly then you are in the right place.</p>
  <p>If you are hearing about the essential new leadership essentials and you are ready to hear how to adopt them into your life or business then you are at the right place.</p>
  <p>I am so convinced that you will be delighted with how fast you can make change happen.</p>
</div>
<a class="btn" style="left:120px; top:612px; width:68px;">Read more</a>
<div class="about-photo" role="img" aria-label="Two businessmen in suits talking at an office table"></div>

<section class="services">
  <article class="service-card" style="left:113px;">
    <h3 class="service-title">CONSULTANCY</h3>
    <svg class="service-icon" width="36" height="32" viewBox="0 0 36 32" fill="var(--muted-icon)">
      <circle cx="9" cy="6" r="4.5"/><circle cx="27" cy="6" r="4.5"/><circle cx="18" cy="11" r="5.5"/>
      <path d="M1 22 q0-8 8-8 q4 0 6 2 q-5 2-5 9 H1Z"/><path d="M35 22 q0-8-8-8 q-4 0-6 2 q5 2 5 9 H35Z"/>
      <path d="M8 31 q0-13 10-13 q10 0 10 13Z"/>
    </svg>
    <ul class="service-list">
      <li class="highlight">Professional and Personal</li>
      <li>Next Generation Leaders (16-30)</li>
      <li>Consultation Options</li>
    </ul>
    <a class="btn">Read more</a>
  </article>

  <article class="service-card" style="left:322px;">
    <h3 class="service-title">ON ASSIGNMENT</h3>
    <svg class="service-icon" width="28" height="28" viewBox="0 0 28 28" fill="none" stroke="var(--muted-icon)" stroke-width="2">
      <rect x="1" y="1" width="26" height="26" rx="1"/>
      <line x1="5" y1="7" x2="23" y2="7"/><rect x="5" y="11" width="5" height="4"/>
      <line x1="13" y1="12" x2="23" y2="12"/><line x1="13" y1="16" x2="23" y2="16"/>
      <line x1="5" y1="20" x2="23" y2="20"/>
    </svg>
    <ul class="service-list">
      <li>Team Cohesion Strategy</li>
      <li>Go To Market Strategy</li>
      <li>Internationalisation Strategy</li>
    </ul>
    <a class="btn">Read more</a>
  </article>

  <article class="service-card" style="left:530px;">
    <h3 class="service-title">PROPERTY:<br>PRIVATE CLIENT</h3>
    <svg class="service-icon" width="34" height="28" viewBox="0 0 34 28">
      <rect x="1" y="1" width="32" height="26" fill="none" stroke="var(--muted-icon)" stroke-width="2"/>
      <circle cx="10" cy="9" r="3" fill="var(--muted-icon)"/>
      <path d="M4 24 L13 15 L18 19 L24 11 L30 24 Z" fill="var(--muted-icon)"/>
    </svg>
    <ul class="service-list">
      <li>Promotion and cash-buyer matching</li>
      <li>Investment: high return projects</li>
      <li>Commercial: Hotels and Senior Housing</li>
      <li>Prestige Residential: US, Australia, UK</li>
    </ul>
    <a class="btn">Read more</a>
  </article>
</section>

<section class="contact-band">
  <p class="contact-heading">Let’s chat, if you want a non committal conversation get in<br>touch by email or telephone</p>
  <div class="contact-bar">
    <svg width="10" height="8" viewBox="0 0 10 8" fill="none" stroke="#e6e2e8" stroke-width="1"><rect x="0.5" y="0.5" width="9" height="7"/><path d="M0.5 0.5 L5 4.5 L9.5 0.5"/></svg>
    <span>Email : Director@brightharborventure.com</span>
    <span class="gap"></span>
    <svg width="9" height="9" viewBox="0 0 9 9" fill="#e6e2e8"><path d="M1.8 0.3 L3.4 2.4 L2.4 3.4 Q3.4 5.6 5.6 6.6 L6.6 5.6 L8.7 7.2 L7.6 8.7 Q1 8 0.3 1.4 Z"/></svg>
    <span>Call : +44 (0) 768 213 5597</span>
  </div>
</section>

<footer class="legal">
  <div class="legal-company">
    <svg width="6" height="9" viewBox="0 0 6 9" fill="#111"><path d="M3 0 A3 3 0 0 1 6 3 C6 5 3 9 3 9 C3 9 0 5 0 3 A3 3 0 0 1 3 0Z"/><circle cx="3" cy="3" r="1.1" fill="var(--mist)"/></svg>
    <span>Company: Bright Harbor Venture Limited, registered in England and Wales. Registeres number 10482915</span>
  </div>
  <p class="legal-copy">© 2016. www.brightharborventure.com</p>
</footer>

</body>
</html>
```